Need Primer (paint) Label Design

THE ATTACHED LABEL/S ARE SOLEY FOR REFERENCE. DO NOT MAKE ME AN INTERIOR PAINT OR CHALK PAINT LABEL. I ONLY NEED A "PRIMER" LABEL. THE ATTACHED INTERIOR PAINT LABEL IS ONLY TO SHOW YOU THE THEME/DESIGN OF OUR OTHER LABELS. THE BLUE LABEL ONLY HAS A DESIGN ASPECT I LIKE (PRIMER ON SIDE). The last four labels are our competitors.
```````````````````````````````````````````````````````````````````````````````````````````````````
We need this label to look professional, sharp, eye catching and modern.
OUR PRIMARY COLORS ARE BLACK AND WHITE. IF YOU INCOPORATE ANOTHER COLOR, SILVER OR GOLD MIGHT BE IDEAL BUT PLEASE DON'T DRIFT TOO FAR.
The attached documents:
1st - Our Logo
2nd - Our chalk paint label (reference). We do not need a chalk paint label.
3rd. A random design example. I like the PRIME on the side running vertically. I think it's a cool design concept.
````````````````````````````````````````````````````````````````````````````````````````````````````
We are going to be using a normal paint can with a metal bail/handle so please use that with you design work
``````````````````````````````````````````````````````````````````````````````````````````````````
Order, in my head:
4376
Coatings
^^ I want this to stand out as well but I don't want it to be the first thing your eye is drawn to. Probably 2nd
Interior/Exterior
Multi - Surface Primer
^^ Want this to stick out and draw your eye so the customer knows what it is immediately
Exceptional Adhesion, Performance, Durability,
Use on Wood, Drywall, Plaster, Stucco, Masonry, Brick, Paneling, Painted Metal, & Properly Prepared Glossy Surfaces & More
35* Lowe Temperature Application (can be on side or small)
100% Acrylic
Low Odor - Low VOC - Soap & Water Clean Up
1 US Gallon - 3.785 L
Feel free to get creative with it!

```html
<!DOCTYPE html>
<html lang="en">
<head>
<meta charset="utf-8">
<title>4376 Coatings – Multi-Surface Primer Label</title>
<link rel="stylesheet" href="https://fonts.googleapis.com/css2?family=Montserrat:wght@500;600;700;800;900&display=swap">
<style>
  :root {
    --ink: #111111;
    --paper: #ffffff;
    --backdrop: #ececec;
    --gold: #c9a96a;
    --rule: #d8d8d8;
  }
  * { box-sizing: border-box; margin: 0; padding: 0; }
  html, body { width: 710px; height: 1200px; overflow: hidden; }
  body {
    background: var(--backdrop);
    font-family: "Montserrat", Arial, sans-serif;
    color: var(--ink);
    position: relative;
  }
  .label {
    position: absolute;
    left: 20px; top: 410px;
    width: 670px; height: 380px;
    background: var(--paper);
    border: 1px solid var(--rule);
    overflow: hidden;
  }
  .top-band {
    position: absolute; left: 0; top: 0;
    width: 530px; height: 16px;
    background: var(--ink);
  }
  /* left column */
  .spec-column {
    position: absolute; left: 14px; top: 108px; width: 136px;
    text-align: center;
  }
  .spec-temp {
    font-weight: 800; font-size: 48px; line-height: 1; letter-spacing: -1px;
  }
  .spec-temp-note {
    font-weight: 600; font-size: 9px; line-height: 1.25; letter-spacing: .6px;
    text-transform: uppercase; margin-top: 6px;
  }
  .spec-acrylic {
    font-weight: 800; font-size: 32px; line-height: 1; margin-top: 20px;
  }
  .spec-acrylic-note {
    font-weight: 800; font-size: 15px; letter-spacing: 1px; margin-top: 2px;
  }
  /* brand + product block */
  .product-block {
    position: absolute; left: 150px; top: 26px; width: 380px;
    text-align: center;
  }
  .brand-name {
    font-family: "Montserrat", Arial, sans-serif; font-weight: 600;
    color: var(--ink);
  }
  .brand-number {
    font-size: 76px; line-height: 1; letter-spacing: 1px;
  }
  .brand-word {
    font-size: 22px; line-height: 1; letter-spacing: 8px; padding-left: 8px;
    margin-top: 4px;
  }
  .product-type {
    font-weight: 800; font-size: 24px; line-height: 1; margin-top: 16px;
  }
  .product-name {
    font-weight: 600; font-size: 16px; letter-spacing: 1px; margin-top: 6px;
  }
  .benefits {
    display: flex; justify-content: center; margin-top: 10px;
  }
  .benefit {
    font-weight: 700; font-size: 9px; line-height: 1.15; letter-spacing: .4px;
    padding: 5px 12px; text-transform: uppercase;
    border-right: 1px solid var(--gold);
    display: flex; align-items: center;
  }
  .benefit:last-child { border-right: none; }
  .care-line {
    font-weight: 800; font-size: 11.5px; letter-spacing: .5px; margin-top: 10px;
  }
  /* bottom bands */
  .volume-box {
    position: absolute; left: 0; bottom: 0;
    width: 142px; height: 64px;
    background: var(--ink); color: var(--paper);
    display: flex; flex-direction: column; justify-content: center; align-items: center;
    font-weight: 700; font-size: 12px; line-height: 1.3; letter-spacing: .5px;
  }
  .surfaces-band {
    position: absolute; left: 150px; bottom: 0;
    width: 380px; height: 64px;
    background: var(--ink); color: var(--paper);
    display: flex; align-items: center; justify-content: center;
    text-align: center; padding: 0 26px;
    font-weight: 600; font-size: 10px; line-height: 1.5; letter-spacing: .6px;
    text-transform: uppercase;
  }
  /* vertical product word */
  .side-word {
    position: absolute; left: 530px; top: 0; width: 140px; height: 380px;
  }
  .side-dot {
    position: absolute; left: 10px; top: 250px;
    width: 16px; height: 16px; border-radius: 50%;
    background: var(--gold);
  }
  .side-word-text {
    position: absolute; left: 80px; top: 190px;
    transform: translate(-50%, -50%) rotate(-90deg);
    font-weight: 900; font-size: 92px; line-height: 1; letter-spacing: -2px;
    white-space: nowrap;
  }
</style>
</head>
<body>
  <section class="label">
    <div class="top-band"></div>

    <div class="spec-column">
      <div class="spec-temp">35*</div>
      <div class="spec-temp-note">Lowe Temperature<br>Application</div>
      <div class="spec-acrylic">100%</div>
      <div class="spec-acrylic-note">ACRYLIC</div>
    </div>

    <div class="product-block">
      <div class="brand-name">
        <div class="brand-number">4376</div>
        <div class="brand-word">COATINGS</div>
      </div>
      <div class="product-type">INTERIOR/EXTERIOR</div>
      <div class="product-name">MULTI - SURFACE PRIMER</div>
      <div class="benefits">
        <span class="benefit">Exceptional<br>Adhesion</span>
        <span class="benefit">Performance</span>
        <span class="benefit">Durability</span>
      </div>
      <div class="care-line">LOW ODOR - LOW VOC - SOAP &amp; WATER CLEAN UP</div>
    </div>

    <div class="volume-box">
      <span>1 US Gallon</span>
      <span>3.785 L</span>
    </div>

    <div class="surfaces-band">
      Use on wood · Drywall · Plaster · Stucco · Masonry · Brick · Paneling · Painted metal · &amp; properly prepared glossy surfaces &amp; more
    </div>

    <div class="side-word">
      <span class="side-dot"></span>
      <span class="side-word-text">Primer</span>
    </div>
  </section>
</body>
</html>
```